Harborline Auto LLC

Car Dealer Customer Service
Address: 2874 Cresthaven Road, Shelbyville, TN 37162
web: www.harborlineautoxq.net
email: harborlineautoxq@mailnest.example
Phone: (931) 555-0148
Phone: (629) 555-0173

```html
<!DOCTYPE html>
<html lang="en">
<head>
<meta charset="utf-8">
<title>Harborline Auto – Business Card</title>
<link rel="stylesheet" href="https://fonts.googleapis.com/css2?family=Poppins:wght@400;600;700&display=swap">
<style>
  :root {
    --bg: #2a2a2a;
    --blue: #1c6e9f;
    --blue-light: #2385b8;
    --blue-deep: #175d88;
    --gold: #e0a43a;
    --paper: #f1f1f1;
    --ink: #1e1e1e;
    --white: #ffffff;
  }
  * { margin: 0; padding: 0; box-sizing: border-box; }
  html, body { width: 1200px; height: 1138px; overflow: hidden; }
  body {
    background: var(--bg);
    font-family: "Poppins", sans-serif;
    position: relative;
  }
  .card {
    position: absolute;
    left: 290px;
    width: 620px;
    height: 374px;
    border-radius: 16px;
    overflow: hidden;
  }
  .card-front {
    top: 186px;
    background: linear-gradient(135deg, var(--blue) 0%, var(--blue-light) 100%);
  }
  .card-back {
    top: 608px;
    background: var(--paper);
  }
  .front-mark {
    position: absolute;
    left: -92px;
    top: 20px;
  }
  .front-name {
    position: absolute;
    right: 42px;
    top: 56px;
    color: var(--white);
    font-weight: 600;
    font-size: 27px;
    letter-spacing: 0.5px;
    text-transform: uppercase;
  }
  .front-web {
    position: absolute;
    right: 42px;
    top: 322px;
    color: var(--white);
    font-size: 14px;
  }
  .back-panel {
    position: absolute;
    left: 0; top: 0;
  }
  .back-brand {
    position: absolute;
    left: 0;
    width: 300px;
    top: 88px;
    text-align: center;
    color: var(--white);
  }
  .back-brand .mark-circle {
    display: block;
    margin: 0 auto 24px;
  }
  .back-brand .brand-name {
    font-weight: 600;
    font-size: 23px;
    letter-spacing: 0.5px;
    text-transform: uppercase;
  }
  .contact {
    position: absolute;
    right: 24px;
    top: 0;
    text-align: right;
  }
  .person-name {
    position: absolute;
    right: 24px;
    top: 44px;
    color: var(--blue-deep);
    font-weight: 700;
    font-size: 24px;
    white-space: nowrap;
  }
  .person-role {
    position: absolute;
    right: 24px;
    top: 78px;
    color: var(--ink);
    font-size: 15px;
    white-space: nowrap;
  }
  .address {
    position: absolute;
    right: 24px;
    top: 205px;
    color: var(--ink);
    font-size: 15px;
    line-height: 22px;
    text-align: right;
    white-space: nowrap;
  }
  .contact-list {
    position: absolute;
    right: 24px;
    top: 259px;
    list-style: none;
  }
  .contact-list li {
    display: flex;
    justify-content: flex-end;
    align-items: center;
    height: 22px;
    gap: 9px;
    font-size: 14.5px;
    color: var(--ink);
    white-space: nowrap;
  }
  .contact-list li.phone {
    color: var(--blue-deep);
    font-weight: 700;
    font-size: 15.5px;
  }
  .contact-list svg { flex: none; }
</style>
</head>
<body>

<section class="card card-front">
  <svg class="front-mark" width="340" height="340" viewBox="0 0 340 340" role="img" aria-label="Brand emblem area">
    <circle cx="170" cy="170" r="150" fill="var(--blue-deep)" stroke="var(--white)" stroke-width="26"/>
  </svg>
  <h1 class="front-name">Harborline Auto</h1>
  <p class="front-web">www.harborlineautoxq.net</p>
</section>

<section class="card card-back">
  <svg class="back-panel" width="330" height="374" viewBox="0 0 330 374" aria-hidden="true">
    <path d="M0 0 H248 C318 100 330 250 252 374 H0 Z" fill="var(--gold)"/>
    <path d="M0 0 H236 C306 100 318 250 244 374 H0 Z" fill="var(--blue)"/>
  </svg>

  <div class="back-brand">
    <svg class="mark-circle" width="130" height="130" viewBox="0 0 130 130" aria-hidden="true">
      <circle cx="65" cy="65" r="56" fill="none" stroke="var(--white)" stroke-width="14"/>
    </svg>
    <p class="brand-name">Harborline Auto</p>
  </div>

  <h2 class="person-name">Dorian Welke</h2>
  <p class="person-role">Managing Director</p>

  <p class="address">2874 Cresthaven Road,<br>Shelbyville, TN 37162</p>

  <ul class="contact-list">
    <li class="phone">931-555-0148
      <svg width="14" height="14" viewBox="0 0 24 24" aria-hidden="true"><path fill="var(--gold)" d="M3 8c0-3 4-5 9-5s9 2 9 5v2h-5V8H8v2H3zM6 12h12l2 8H4z"/></svg>
    </li>
    <li class="phone">629-555-0173
      <svg width="14" height="14" viewBox="0 0 24 24" aria-hidden="true"><path fill="var(--gold)" d="M3 8c0-3 4-5 9-5s9 2 9 5v2h-5V8H8v2H3zM6 12h12l2 8H4z"/></svg>
    </li>
    <li>www.harborlineautoxq.net
      <svg width="14" height="14" viewBox="0 0 24 24" aria-hidden="true"><rect x="2" y="5" width="20" height="14" fill="var(--gold)"/><path d="M2 5l10 8 10-8" fill="none" stroke="var(--paper)" stroke-width="1.8"/></svg>
    </li>
    <li>harborlineautoxq@mailnest.example
      <svg width="14" height="14" viewBox="0 0 24 24" aria-hidden="true"><circle cx="12" cy="12" r="10" fill="var(--gold)"/><path d="M2 12h20M12 2c4 4 4 16 0 20M12 2c-4 4-4 16 0 20" fill="none" stroke="var(--paper)" stroke-width="1.4"/></svg>
    </li>
  </ul>
</section>

</body>
</html>
```